Mental Health care Company in Washington DC

We are a new mental health care services provider in Washington DC. Please look at these sites.
https://brightwaterfamilysupport.com
https://www.quietharborinc.com
https://willowgate-dc.org/
https://www.tidepathdc.com
https://www.thelanternofdc.com

```html
<!DOCTYPE html>
<html lang="en">
<head>
<meta charset="utf-8">
<title>Calmwell Care – Mental Wellness in Washington DC</title>
<link href="https://fonts.googleapis.com/css2?family=Figtree:wght@400;500;600;700;800&family=Inter:wght@400;500;600&display=swap" rel="stylesheet">
<style>
:root{
  --navy:#0f1f3d;
  --navy-soft:#1b2d52;
  --orange:#f47c20;
  --orange-soft:#f9a25c;
  --teal:#6fcbdc;
  --peach:#fde9dc;
  --grey-bg:#f1f1f1;
  --line:#e4e4e4;
  --text:#222;
  --white:#fff;
}
*{box-sizing:border-box;margin:0;padding:0}
html,body{width:1200px;height:4528px;overflow:hidden}
body{position:relative;background:var(--white);font-family:"Inter",sans-serif;color:var(--text)}
.abs{position:absolute}
h1,h2,h3,h4{font-family:"Figtree",sans-serif}
p{line-height:1.55}

.topbar{left:475px;top:0;width:725px;height:32px;background:var(--navy);color:#fff;font-size:11px;display:flex;align-items:center;gap:28px;padding-left:70px}
.topbar::before{content:"";position:absolute;left:0;top:0;width:22px;height:32px;background:var(--orange);transform:skewX(25deg);transform-origin:top left}
.topbar span{display:flex;align-items:center;gap:6px}
.topbar svg{width:12px;height:12px}

.brand{font-family:"Figtree",sans-serif;font-weight:600;font-size:30px;color:var(--navy);line-height:1;white-space:nowrap}
.header-brand{left:91px;top:40px}

.nav{left:553px;top:54px;font-size:13px;color:var(--navy)}
.nav a{text-decoration:none;color:inherit;position:absolute;white-space:nowrap}
.nav .active{color:var(--orange)}
.btn{display:inline-flex;align-items:center;justify-content:center;background:var(--orange);color:#fff;border-radius:22px;font-weight:600;font-size:12px;text-decoration:none}
.cta-top{left:994px;top:47px;width:108px;height:30px}

.hero{left:0;top:91px;width:1200px;height:664px;background:linear-gradient(100deg,#2b2f33 0%,#4a4f53 35%,#8b8d8c 60%,#d8d6d2 100%)}
.hero-person{left:690px;top:130px;width:450px;height:560px;border-radius:200px 200px 0 0;background:linear-gradient(180deg,#8b5e45 0%,#f1f1f3 35%,#e9eaee 100%);opacity:.55}
.hero-wave{left:0;top:560px;width:1200px;height:200px}
.hero-kicker{left:141px;top:216px;color:#fff;font-size:22px;font-family:"Figtree",sans-serif;font-weight:500;letter-spacing:.5px}
.hero-title{left:141px;top:250px;color:#fff;font-size:44px;font-weight:800;line-height:58px;letter-spacing:.3px}
.hero-title .teal{color:var(--teal)}
.hero-text{left:141px;top:376px;width:400px;color:#fff;font-size:15.5px;line-height:23px}
.hero-btn{left:141px;top:471px;width:199px;height:40px;border-radius:20px;font-size:12.5px;gap:8px}
.scroll-down{left:572px;top:701px;width:56px;height:56px;border-radius:50%;background:#fff;box-shadow:0 4px 14px rgba(0,0,0,.12);display:flex;align-items:center;justify-content:center}

.kicker{font-family:"Figtree",sans-serif;font-weight:600;font-size:17px;color:var(--navy);display:flex;align-items:center;gap:6px;letter-spacing:.3px}
.kicker .orange{color:var(--orange)}
.kicker .spark{width:16px;height:16px}
.kicker .tail{width:60px;height:1px;background:#c9ccd3}
.center{left:0;width:1200px;justify-content:center}

.about-main{left:141px;top:879px;width:355px;height:265px;background:linear-gradient(160deg,#d9e1ea 0%,#7c93b0 45%,#2f4f7a 100%)}
.about-small{left:404px;top:1014px;width:155px;height:160px;background:linear-gradient(160deg,#c8d6e0 0%,#8fa9a6 50%,#5c7c8c 100%);border:4px solid #fff}
.about-col{left:606px;top:843px;width:412px}
.about-col h2{font-size:30px;font-weight:700;color:var(--navy);line-height:41px;margin-top:18px}
.about-col h2 .orange{color:var(--orange)}
.about-col p{font-size:11px;color:#333;line-height:18.5px;margin-top:12px}
.read-more{display:inline-flex;align-items:center;gap:6px;font-size:12.5px;font-weight:600;color:var(--navy);text-decoration:underline}
.read-more.o{color:var(--orange)}
.about-col .read-more{margin-top:18px}

.services-bg{left:0;top:1262px;width:1200px;height:611px;background:var(--grey-bg)}
.services-title{left:0;top:1372px;width:1200px;text-align:center;font-size:27px;font-weight:700;color:var(--navy)}
.services-title .orange{color:var(--orange)}
.svc-card{top:1428px;width:289px;height:366px;background:#fff;border-radius:8px;overflow:hidden;box-shadow:0 2px 10px rgba(0,0,0,.05);text-align:center}
.svc-img{height:206px}
.svc-icon{position:absolute;left:116px;top:178px;width:56px;height:56px;border-radius:50%;border:4px solid #fff;display:flex;align-items:center;justify-content:center}
.svc-card h3{font-size:16px;font-weight:600;color:var(--navy);margin-top:42px}
.svc-card p{font-size:11.5px;color:#444;width:220px;margin:8px auto 0;line-height:18px}
.svc-card .read-more{margin-top:16px;font-size:12px}

.why-ring{left:438px;top:2039px;width:324px;height:324px;border-radius:50%;border:7px solid var(--orange);padding:8px;background:#fff}
.why-ring div{width:100%;height:100%;border-radius:50%;background:radial-gradient(circle at 50% 60%,#d9a79a 0%,#c99b93 18%,#e9ecef 45%,#b9c3cc 100%)}
.why-item{width:260px}
.why-item h4{font-size:15.5px;font-weight:600;color:var(--navy)}
.why-item p{font-size:11.5px;color:#444;line-height:18px;margin-top:6px}
.why-item.r{text-align:right}
.num{width:25px;height:25px;border-radius:50%;color:#fff;font-size:11px;font-weight:600;display:flex;align-items:center;justify-content:center}
.num.n{background:var(--navy)}
.num.o{background:var(--orange)}

.stats{left:141px;top:2548px;width:917px;height:140px;background:var(--orange);border-radius:8px;display:flex;align-items:center;color:#fff;text-align:center}
.stat{flex:1;border-right:1px solid rgba(255,255,255,.55);height:84px;display:flex;flex-direction:column;justify-content:center}
.stat:last-child{border-right:none}
.stat strong{font-family:"Figtree",sans-serif;font-size:40px;font-weight:700;line-height:1}
.stat span{font-size:13px;margin-top:8px}

.blog-card{top:2823px;width:230px;height:317px;background:#fff;border-radius:4px;box-shadow:0 2px 10px rgba(0,0,0,.08);overflow:hidden}
.blog-card .img{height:158px}
.blog-card .body{padding:16px}
.blog-card h4{font-size:15px;font-weight:600;color:var(--navy)}
.blog-card p{font-size:10.5px;color:#555;line-height:17px;margin-top:6px}
.blog-card .read-more{position:absolute;left:16px;bottom:26px;font-size:12px}
.blog-card.feature{background:var(--navy);padding:44px 16px 0}
.blog-card.feature h4{color:#fff;font-size:16px;line-height:23px}
.blog-card.feature p{color:#d9deea;margin-top:14px}
.blog-card.fade{opacity:.55}
.arrow{width:28px;height:14px}

.ins-table{left:141px;top:3250px;width:917px;border:1px solid var(--line);border-collapse:collapse;font-size:11.5px}
.ins-table th{background:var(--peach);font-weight:500;color:var(--navy);text-align:left;height:40px;font-size:12px}
.ins-table td{height:44px;color:#555;border-top:1px solid var(--line)}
.ins-table tr:nth-child(even) td{background:#f6f6f6}
.ins-table th:first-child,.ins-table td:first-child{padding-left:39px;width:432px}
.ins-table th:nth-child(2),.ins-table td:nth-child(2){width:349px}

.testi-bg{left:0;top:3535px;width:1200px;height:448px;background:#ebebeb}
.t-card{top:3654px;width:239px;height:233px;background:#fff;border-radius:4px;padding:26px 16px}
.stars{color:var(--orange);font-size:13px;letter-spacing:2px}
.t-card p{font-size:10.5px;color:#444;line-height:18px;margin-top:6px}
.t-person{display:flex;align-items:center;gap:12px;margin-top:14px}
.avatar{width:46px;height:46px;border-radius:50%;background:linear-gradient(135deg,#e2d6cf,#9d8a80)}
.t-person strong{font-family:"Figtree",sans-serif;font-size:16px;color:var(--navy);font-weight:700;display:block}
.t-person span{font-size:11px;color:var(--navy-soft);font-weight:500}
.dots{left:585px;top:3903px;display:flex;gap:3px}
.dots i{width:3px;height:3px;border-radius:50%;background:var(--orange)}

.newsletter{left:0;top:3983px;width:1200px;height:278px;background:var(--orange)}
.nl-title{left:141px;top:4068px;color:#fff;font-size:28px;font-weight:700}
.nl-text{left:141px;top:4114px;width:400px;color:#fff;font-size:13.5px;line-height:21px}
.nl-form{left:655px;top:4094px;width:404px;height:56px;border-radius:8px;background:var(--orange-soft);overflow:hidden;display:flex}
.nl-form span{flex:1;color:#fff;font-size:12px;display:flex;align-items:center;padding-left:24px}
.nl-form b{width:102px;background:#fff;color:var(--navy);font-size:12px;display:flex;align-items:center;justify-content:center;font-weight:600}

.footer{left:0;top:4261px;width:1200px;height:267px;background:var(--navy);color:#fff}
.footer .brand{color:#fff}
.f-desc{left:144px;top:140px;width:232px;font-size:9.5px;line-height:16px;color:#d3d9e6}
.f-col h5{font-family:"Figtree",sans-serif;font-size:13px;font-weight:600;margin-bottom:14px}
.f-col a{display:block;font-size:10px;color:#d3d9e6;text-decoration:none;height:24.5px}
.f-contact div{display:flex;align-items:center;gap:8px;font-size:10px;color:#d3d9e6;height:28px}
.social{display:flex;gap:16px;margin-top:14px}
.social i{width:16px;height:16px;border-radius:50%;background:#fff;display:block}
.copy{left:0;top:238px;width:1200px;text-align:center;font-size:9px;color:#d3d9e6}
</style>
</head>
<body>

<div class="abs topbar">
  <span><svg viewBox="0 0 24 24" fill="#f47c20"><path d="M6.6 10.8a15 15 0 0 0 6.6 6.6l2.2-2.2c.3-.3.7-.4 1-.2 1.1.4 2.3.6 3.6.6.6 0 1 .4 1 1V20c0 .6-.4 1-1 1A17 17 0 0 1 3 4c0-.6.4-1 1-1h3.5c.6 0 1 .4 1 1 0 1.3.2 2.5.6 3.6.1.3 0 .7-.2 1z"/></svg>Call now: <b>(202) 555-0148</b></span>
  <span><svg viewBox="0 0 24 24"><path d="M2 5h20v14H2z" fill="#f47c20"/><path d="M2 5l10 8 10-8" stroke="#0f1f3d" stroke-width="2" fill="none"/></svg>Email: <b>hello@calmwellcare.com</b></span>
  <span><svg viewBox="0 0 24 24"><circle cx="12" cy="12" r="10" fill="#f47c20"/><path d="M12 6v6l4 2" stroke="#0f1f3d" stroke-width="2" fill="none"/></svg>Time: <b>Mon - Sun, 08:30am to 05:30pm</b></span>
</div>

<div class="abs brand header-brand">Calmwell Care</div>
<nav class="abs nav">
  <a class="active" href="#" style="left:0">Home</a>
  <a href="#" style="left:74px">About Us</a>
  <a href="#" style="left:169px">Services ▾</a>
  <a href="#" style="left:273px">Blog</a>
  <a href="#" style="left:338px">FAQs</a>
</nav>
<a class="abs btn cta-top" href="#">Contact Now</a>

<section class="abs hero" role="img" aria-label="Photo of a smiling doctor in a white coat with a stethoscope, arms crossed, in a bright clinic"></section>
<div class="abs hero-person" aria-hidden="true"></div>
<svg class="abs hero-wave" viewBox="0 0 1200 200" preserveAspectRatio="none"><path d="M0 70 C180 30 320 30 460 90 C600 150 760 150 900 90 C1020 40 1120 40 1200 60 L1200 200 L0 200Z" fill="#fff"/></svg>
<div class="abs hero-kicker">COMPASSIONATE</div>
<h1 class="abs hero-title">MENTAL <span class="teal">WELLNESS</span> IN<br>WASHINGTON DC</h1>
<p class="abs hero-text">Evidence-based care tailored to your needs. Where clinical expertise meets your unique needs</p>
<a class="abs btn hero-btn" href="#"><svg width="14" height="14" viewBox="0 0 24 24" fill="#fff"><path d="M4 5h16v15H4z"/><path d="M4 9h16" stroke="#f47c20" stroke-width="2"/></svg>BOOK APPOINTMENT</a>
<div class="abs scroll-down"><svg width="20" height="28" viewBox="0 0 20 28"><path d="M10 2v22M3 17l7 7 7-7" stroke="#f47c20" stroke-width="2" fill="none"/></svg></div>

<div class="abs about-main" role="img" aria-label="Photo of a team of doctors and nurses walking down a hospital corridor"></div>
<div class="abs about-small" role="img" aria-label="Photo of a clinician in scrubs with a stethoscope"></div>
<div class="abs about-col">
  <div class="kicker">ABOUT <span class="orange">US</span> <svg class="spark" viewBox="0 0 16 16"><path d="M8 0v16M0 8h16" stroke="#6fcbdc" stroke-width="2"/><path d="M8 3v10M3 8h10" stroke="#f47c20" stroke-width="2"/></svg><span class="tail"></span></div>
  <h2>Your Path to Peaceful<br>Wellness in the <span class="orange">Heart of DC</span></h2>
  <p>Lorem Ipsum is simply dummy text of the printing and typesetting industry. Lorem Ipsum has been the industry's standard dummy text ever since the 1500s, when an unknown printer took a galley of type and scrambled it to make a type specimen book. It has survived not only five centuries,</p>
  <p>Lorem Ipsum is simply dummy text of the printing and typesetting industry. Lorem Ipsum has been the industry's</p>
  <p>when an unknown printer took a galley of type and scrambled it to make a type specimen book. It has survived not only five centuries, but also the leap into electronic typesetting, remaining essentially unchanged</p>
  <a class="read-more" href="#">Read More <svg width="20" height="10" viewBox="0 0 20 10"><path d="M0 5h17M13 1l4 4-4 4" stroke="#f47c20" stroke-width="2" fill="none"/></svg></a>
</div>

<div class="abs services-bg"></div>
<div class="abs kicker center" style="top:1340px">OUR CORE SERVICES <svg class="spark" viewBox="0 0 16 16"><path d="M8 0v16M0 8h16" stroke="#6fcbdc" stroke-width="2"/><path d="M8 3v10M3 8h10" stroke="#f47c20" stroke-width="2"/></svg></div>
<h2 class="abs services-title">Your Path to Wellness <span class="orange">Starts Here.</span></h2>

<article class="abs svc-card" style="left:141px">
  <div class="svc-img" role="img" aria-label="Photo of a therapist talking with a client in an office" style="background:linear-gradient(135deg,#6b6a63,#b7b3a8 55%,#2e3a4a)"></div>
  <div class="svc-icon" style="background:var(--navy)"><svg width="22" height="22" viewBox="0 0 24 24" fill="none" stroke="#fff" stroke-width="1.8"><circle cx="12" cy="10" r="6"/><path d="M9 20h6M12 16v4"/></svg></div>
  <h3>Individual Therapy</h3>
  <p>Lorem Ipsum is simply dummy printing and typesetting industry.</p>
  <a class="read-more o" href="#">Read More <svg width="20" height="10" viewBox="0 0 20 10"><path d="M0 5h17M13 1l4 4-4 4" stroke="#f47c20" stroke-width="1.6" fill="none"/></svg></a>
</article>
<article class="abs svc-card" style="left:455px">
  <div class="svc-img" role="img" aria-label="Photo of people seated in a circle during a group session" style="background:linear-gradient(135deg,#5a4a3e,#a88f76 55%,#3b342e)"></div>
  <div class="svc-icon" style="background:var(--orange)"><svg width="24" height="22" viewBox="0 0 24 22" fill="none" stroke="#fff" stroke-width="1.8"><circle cx="7" cy="7" r="3"/><circle cx="17" cy="7" r="3"/><path d="M2 19c0-4 3-6 5-6s5 2 5 6M12 19c0-4 3-6 5-6s5 2 5 6"/></svg></div>
  <h3>Group Sessions</h3>
  <p>Lorem Ipsum is simply dummy printing and typesetting industry.</p>
  <a class="read-more o" href="#">Read More <svg width="20" height="10" viewBox="0 0 20 10"><path d="M0 5h17M13 1l4 4-4 4" stroke="#f47c20" stroke-width="1.6" fill="none"/></svg></a>
</article>
<article class="abs svc-card" style="left:770px">
  <div class="svc-img" role="img" aria-label="Photo of specialists working with monitors in a clinical lab" style="background:linear-gradient(135deg,#dfe8f0,#6f8fb5 50%,#24406e)"></div>
  <div class="svc-icon" style="background:var(--navy)"><svg width="20" height="22" viewBox="0 0 20 22" fill="none" stroke="#fff" stroke-width="1.8"><circle cx="10" cy="6" r="4"/><path d="M2 21c0-5 4-8 8-8s8 3 8 8z"/></svg></div>
  <h3>Specialized Programs</h3>
  <p>Lorem Ipsum is simply dummy printing and typesetting industry.</p>
  <a class="read-more o" href="#">Read More <svg width="20" height="10" viewBox="0 0 20 10"><path d="M0 5h17M13 1l4 4-4 4" stroke="#f47c20" stroke-width="1.6" fill="none"/></svg></a>
</article>

<div class="abs kicker center" style="top:1952px">WHY CHOOSE US <svg class="spark" viewBox="0 0 16 16"><path d="M8 0v16M0 8h16" stroke="#6fcbdc" stroke-width="2"/><path d="M8 3v10M3 8h10" stroke="#f47c20" stroke-width="2"/></svg><span class="tail" style="width:80px"></span></div>
<div class="abs why-ring"><div role="img" aria-label="Photo of hands in white coat sleeves holding a model of a human brain"></div></div>

<div class="abs why-item r" style="left:118px;top:2026px"><h4>Individual Therapy</h4><p>Lorem Ipsum is simply dummy printing<br>and typesetting industry.</p></div>
<div class="abs num n" style="left:392px;top:2031px">1</div>
<div class="abs why-item r" style="left:65px;top:2178px"><h4>Individual Therapy</h4><p>Lorem Ipsum is simply dummy printing<br>and typesetting industry.</p></div>
<div class="abs num o" style="left:338px;top:2183px">3</div>
<div class="abs why-item r" style="left:118px;top:2330px"><h4>Individual Therapy</h4><p>Lorem Ipsum is simply dummy printing<br>and typesetting industry.</p></div>
<div class="abs num n" style="left:392px;top:2335px">5</div>

<div class="abs num n" style="left:771px;top:2031px">2</div>
<div class="abs why-item" style="left:807px;top:2026px"><h4>Individual Therapy</h4><p>Lorem Ipsum is simply dummy printing<br>and typesetting industry.</p></div>
<div class="abs num o" style="left:824px;top:2183px">4</div>
<div class="abs why-item" style="left:861px;top:2178px"><h4>Individual Therapy</h4><p>Lorem Ipsum is simply dummy printing<br>and typesetting industry.</p></div>
<div class="abs num n" style="left:771px;top:2335px">6</div>
<div class="abs why-item" style="left:807px;top:2330px"><h4>Individual Therapy</h4><p>Lorem Ipsum is simply dummy printing<br>and typesetting industry.</p></div>

<div class="abs num o" style="left:587px;top:2408px">7</div>
<div class="abs why-item" style="left:470px;top:2444px;text-align:center"><h4>Individual Therapy</h4><p>Lorem Ipsum is simply dummy printing<br>and typesetting industry.</p></div>

<div class="abs stats">
  <div class="stat"><strong>200+</strong><span>Happy Customer</span></div>
  <div class="stat"><strong>10+</strong><span>Branches</span></div>
  <div class="stat"><strong>43+</strong><span>Doctor Team</span></div>
  <div class="stat"><strong>24/7</strong><span>Available</span></div>
</div>

<div class="abs kicker center" style="top:2774px">OUR BLOG <svg class="spark" viewBox="0 0 16 16"><path d="M8 0v16M0 8h16" stroke="#6fcbdc" stroke-width="2"/><path d="M8 3v10M3 8h10" stroke="#f47c20" stroke-width="2"/></svg><span class="tail" style="width:80px"></span></div>
<svg class="abs arrow" style="left:96px;top:2975px" viewBox="0 0 28 14"><path d="M28 7H2M8 1L2 7l6 6" stroke="#0f1f3d" stroke-width="2" fill="none"/></svg>

<article class="abs blog-card feature" style="left:141px">
  <h4>Lorem Ipsum Is Simply Dummy Text Of The Printing</h4>
  <p>It is a long established fact that a reader will be distracted by the readable content of a page when looking at its layout. The point of using Lorem Ipsum is that it has a more its layout.</p>
  <a class="read-more o" href="#">Read More <svg width="20" height="10" viewBox="0 0 20 10"><path d="M0 5h17M13 1l4 4-4 4" stroke="#fff" stroke-width="1.6" fill="none"/></svg></a>
</article>
<article class="abs blog-card" style="left:392px">
  <div class="img" role="img" aria-label="Photo of a doctor studying brain scans on glowing screens" style="background:linear-gradient(135deg,#0d2240,#2f5e8f 55%,#9fc6e6)"></div>
  <div class="body"><h4>Mind Pain</h4><p>It is a long established fact that a reader will be distracted by the readable content.</p></div>
  <a class="read-more o" href="#">Read More <svg width="20" height="10" viewBox="0 0 20 10"><path d="M0 5h17M13 1l4 4-4 4" stroke="#f47c20" stroke-width="1.6" fill="none"/></svg></a>
</article>
<article class="abs blog-card" style="left:643px">
  <div class="img" role="img" aria-label="Photo of a woman relaxing outdoors among green trees" style="background:linear-gradient(135deg,#3e5a2e,#8aa866 50%,#2c3b22)"></div>
  <div class="body"><h4>Mind Fresh Every Day</h4><p>It is a long established fact that a reader will be distracted by the readable content.</p></div>
  <a class="read-more o" href="#">Read More <svg width="20" height="10" viewBox="0 0 20 10"><path d="M0 5h17M13 1l4 4-4 4" stroke="#f47c20" stroke-width="1.6" fill="none"/></svg></a>
</article>
<article class="abs blog-card fade" style="left:893px">
  <div class="img" role="img" aria-label="Photo of a bright, empty hospital room" style="background:linear-gradient(135deg,#e8e6e2,#b8b5ae 60%,#8c8a86)"></div>
  <div class="body"><h4 style="color:var(--orange)">Lorem Ipsum</h4><p>It is a long established fact that a reader will be distracted by the readable content.</p></div>
  <a class="read-more o" href="#">Read More <svg width="20" height="10" viewBox="0 0 20 10"><path d="M0 5h17M13 1l4 4-4 4" stroke="#f47c20" stroke-width="1.6" fill="none"/></svg></a>
</article>
<svg class="abs arrow" style="left:1075px;top:2975px" viewBox="0 0 28 14"><path d="M0 7h26M20 1l6 6-6 6" stroke="#0f1f3d" stroke-width="2" fill="none"/></svg>

<div class="abs kicker center" style="top:3212px">INSURANCE &amp; COST <svg class="spark" viewBox="0 0 16 16"><path d="M8 0v16M0 8h16" stroke="#6fcbdc" stroke-width="2"/><path d="M8 3v10M3 8h10" stroke="#f47c20" stroke-width="2"/></svg><span class="tail" style="width:80px"></span></div>
<table class="abs ins-table">
  <thead><tr><th>Accepted Insurers</th><th>Self-Pay Options</th><th>Sliding Scale</th></tr></thead>
  <tbody>
    <tr><td>Northline, Crestpoint, Summit Mutual</td><td>$150/session</td><td>Available</td></tr>
    <tr><td>Northline, Crestpoint, Summit Mutual</td><td>$1120/session</td><td>No Available</td></tr>
    <tr><td>Northline, Crestpoint, Summit Mutual</td><td>$50/session</td><td>Available</td></tr>
    <tr><td>Northline, Crestpoint, Summit Mutual</td><td>$1140/session</td><td>No Available</td></tr>
  </tbody>
</table>

<div class="abs testi-bg"></div>
<div class="abs kicker center" style="top:3610px">TESTIMONIALS <svg class="spark" viewBox="0 0 16 16"><path d="M8 0v16M0 8h16" stroke="#6fcbdc" stroke-width="2"/><path d="M8 3v10M3 8h10" stroke="#f47c20" stroke-width="2"/></svg><span class="tail" style="width:50px"></span></div>
<svg class="abs arrow" style="left:141px;top:3762px" viewBox="0 0 28 14"><path d="M28 7H2M8 1L2 7l6 6" stroke="#0f1f3d" stroke-width="2" fill="none"/></svg>
<article class="abs t-card" style="left:213px">
  <div class="stars">★★★★</div>
  <p>... followed by some bogus content. Aenean commodo ligula egget dolor. Aenean massa. Cum sociis natoque penatibus et magnis dis parturient montes, nascetur ridiculus mus.</p>
  <div class="t-person"><div class="avatar" role="img" aria-label="Client portrait"></div><div><strong>Maya Linden</strong><span>CEO, Company</span></div></div>
</article>
<article class="abs t-card" style="left:480px">
  <div class="stars">★★★★</div>
  <p>... followed by some bogus content. Aenean commodo ligula egget dolor. Aenean massa. Cum sociis natoque penatibus et magnis dis parturient montes, nascetur ridiculus mus.</p>
  <div class="t-person"><div class="avatar" role="img" aria-label="Client portrait"></div><div><strong>Maya Linden</strong><span>CEO, Company</span></div></div>
</article>
<article class="abs t-card" style="left:748px">
  <div class="stars">★★★★</div>
  <p>... followed by some bogus content. Aenean commodo ligula egget dolor. Aenean massa. Cum sociis natoque penatibus et magnis dis parturient montes, nascetur ridiculus mus.</p>
  <div class="t-person"><div class="avatar" role="img" aria-label="Client portrait"></div><div><strong>Maya Linden</strong><span>CEO, Company</span></div></div>
</article>
<svg class="abs arrow" style="left:1031px;top:3762px" viewBox="0 0 28 14"><path d="M0 7h26M20 1l6 6-6 6" stroke="#0f1f3d" stroke-width="2" fill="none"/></svg>
<div class="abs dots"><i></i><i></i><i></i><i></i><i></i></div>

<section class="abs newsletter"></section>
<h2 class="abs nl-title">Subcribe to our Newsletter</h2>
<p class="abs nl-text">Subscribe for Updates: Stay informed about the latest investor updates, financial results, and announcements by subscribing to our newsletter.</p>
<div class="abs nl-form"><span>Enter your email</span><b>Subscribe</b></div>

<footer class="abs footer">
  <div class="abs brand" style="left:143px;top:62px">Calmwell Care</div>
  <p class="abs f-desc">Lorem Ipsum is simply dummy text of the printing and typesetting industry. Lorem Ipsum has been the industry's standard dummy text ever since the 1500s.</p>
  <div class="abs f-col" style="left:497px;top:48px">
    <h5>Quick &nbsp;link</h5>
    <a href="#">Home</a><a href="#">About Us</a><a href="#">Services</a><a href="#">Blog</a><a href="#">Contact Us</a>
  </div>
  <div class="abs f-col" style="left:696px;top:48px">
    <h5>Services</h5>
    <a href="#">Individual Therapy</a><a href="#">Group Sessions</a><a href="#">Specialized Programs</a><a href="#">24/7 Available</a>
  </div>
  <div class="abs f-col f-contact" style="left:931px;top:48px">
    <h5>Contact Details</h5>
    <div><svg width="12" height="12" viewBox="0 0 24 24" fill="#f47c20"><path d="M6.6 10.8a15 15 0 0 0 6.6 6.6l2.2-2.2c.3-.3.7-.4 1-.2 1.1.4 2.3.6 3.6.6.6 0 1 .4 1 1V20c0 .6-.4 1-1 1A17 17 0 0 1 3 4c0-.6.4-1 1-1h3.5c.6 0 1 .4 1 1 0 1.3.2 2.5.6 3.6.1.3 0 .7-.2 1z"/></svg>(202) 555-0148</div>
    <div><svg width="12" height="12" viewBox="0 0 24 24"><path d="M2 5h20v14H2z" fill="#f47c20"/><path d="M2 5l10 8 10-8" stroke="#0f1f3d" stroke-width="2" fill="none"/></svg>hello@calmwellcare.com</div>
    <div class="social"><i></i><i></i><i></i><i></i></div>
  </div>
  <div class="abs copy">Calmwell Care © Copyright Calmwell Care. All Rights Reserved</div>
</footer>

</body>
</html>
```